Meridale Real Estate

We are looking for help with web design for a new company that is revolutionizing the real estate world on the listing side: by charing per hour for top level professional real estate services. We would like the concept to be simple, clean and easily understood.
Updates

We want this website to actually function, not just a static design.

Industry/Entity Type

Real Estate

```html
<!DOCTYPE html>
<html lang="en">
<head>
<meta charset="utf-8">
<title>Meridale Real Estate</title>
<link href="https://fonts.googleapis.com/css2?family=Arimo:ital,wght@0,400;0,700;1,400&family=Lato:wght@400;700&display=swap" rel="stylesheet">
<style>
:root{
  --teal:#13a9ab;
  --teal-dark:#0e8f91;
  --ink:#222;
  --body:#555;
  --rule:#d8d8d8;
  --white:#fff;
  --footer:#2c2c2c;
  --footer-deep:#1b1b1b;
  --footer-text:#e6e6e6;
  --orange:#f39a1e;
  --orange-deep:#e0700a;
  --logo:#c48a5c;
}
*{box-sizing:border-box;margin:0;padding:0}
html,body{width:741px;height:1200px;overflow:hidden;background:var(--white)}
body{position:relative;font-family:Arimo,Arial,sans-serif;color:var(--ink)}
.abs{position:absolute}

/* header */
.site-header{position:absolute;left:0;top:0;width:741px;height:52px;background:var(--white);z-index:3}
.brand{position:absolute;left:104px;top:-8px;width:78px;height:94px;border-radius:50%;background:var(--white);z-index:4;display:flex;align-items:center;justify-content:center;text-align:center;font-family:Lato,sans-serif;font-size:9px;line-height:12px;letter-spacing:2px;color:var(--logo);text-transform:uppercase;padding-top:12px}
.main-nav{position:absolute;left:273px;top:0;height:52px;display:flex;font-size:12px;color:var(--ink)}
.main-nav a{display:block;height:52px;line-height:58px;padding:0 9px;color:inherit;text-decoration:none;margin-right:1px}
.main-nav a.active{background:var(--teal);color:var(--white);padding:0 6px}

/* hero */
.hero{position:absolute;left:0;top:52px;width:741px;height:305px;overflow:hidden}
.hero-photo{position:absolute;inset:0;background:
  radial-gradient(ellipse at 45% 50%,#e2b36b 0%,#b9813f 25%,#5d4030 50%,transparent 70%),
  linear-gradient(180deg,#3a5b86 0%,#5f6e86 40%,#4c3b2d 70%,#2a2a1e 100%)}
.hero-arrow{position:absolute;top:117px;width:26px;height:26px;border-radius:50%;background:rgba(0,0,0,.35)}
.hero-arrow svg{display:block}
.hero-caption{position:absolute;left:0;bottom:0;width:741px;height:34px;background:rgba(0,0,0,.55);color:var(--white);font-family:Lato,sans-serif;font-size:12.5px;letter-spacing:1.4px;line-height:34px;padding-left:107px}
.hero-dots{position:absolute;right:175px;top:13px;display:flex;gap:2px}
.hero-dots i{display:block;width:6px;height:6px;border-radius:50%;background:#0f4b4c}
.hero-dots i:first-child{background:var(--teal)}

.quick-search{position:absolute;left:461px;top:16px;width:177px;height:250px;background:rgba(255,255,255,.82);border-radius:5px;padding:10px 16px 0 16px;font-size:8px;color:#222}
.quick-search h2{font-family:Lato,sans-serif;font-weight:400;font-size:13px;color:var(--teal);margin-bottom:8px}
.field{height:14px;border:1px solid #888;background:var(--white);padding:0 3px;line-height:12px;position:relative}
.field::after{content:"";position:absolute;right:4px;top:4px;border:3px solid transparent;border-top:4px solid #222}
.field-row{display:flex;justify-content:space-between;margin-top:8px}
.field-row .field{width:64px;margin:0}
.radios{display:flex;gap:14px;margin:10px 0 0 6px;color:var(--teal);align-items:center}
.radio{display:flex;align-items:center;gap:3px}
.radio i{width:12px;height:12px;border-radius:50%;border:1px solid #888;background:#eee;display:block}
.radio i.on{background:radial-gradient(circle,#333 0 3px,#eee 3.5px)}
.suburbs{margin-top:7px;height:50px;border:1px solid #888;background:var(--white);line-height:10.5px;padding-left:2px;position:relative;overflow:hidden}
.suburbs span{display:block}
.suburbs span.sel{background:#d3d3d3}
.suburbs::after{content:"";position:absolute;right:0;top:0;width:8px;height:100%;background:#e6e6e6;border-left:1px solid #bbb}
.search-btn{position:absolute;right:18px;bottom:8px;width:59px;height:21px;background:var(--teal);color:var(--white);border-radius:3px;text-align:center;line-height:21px;font-size:9px}

/* welcome */
.welcome-photo{left:107px;top:382px;width:180px;height:111px;background:linear-gradient(180deg,#4b4f7c 0%,#8d7fa0 40%,#c9a77a 60%,#3a3c48 100%)}
.welcome-title{left:312px;top:381px;font-size:15px;font-weight:400;color:#111}
.welcome-text{left:312px;top:404px;width:326px;font-size:6.6px;line-height:15.4px;color:var(--body)}
.rule{left:107px;top:514px;width:529px;height:1px;background:var(--rule)}

/* featured */
.section-title{left:0;width:741px;text-align:center;font-size:14.5px;font-weight:400;color:#111}
.section-intro{left:130px;width:481px;text-align:center;font-size:7.4px;line-height:17px;color:var(--body)}
.pager{left:618px;top:581px;display:flex;gap:5px}
.card{top:602px;width:120px}
.card-photo{height:103px}
.card h3{font-size:6.8px;font-weight:700;margin-top:11px;color:#111}
.card p{font-size:6.4px;line-height:11.5px;color:var(--body);margin-top:3px}
.more-btn{display:block;width:47px;height:15px;margin-top:9px;border:1px solid #c8c8c8;border-radius:2px;background:linear-gradient(#f7f7f7,#dcdcdc);font-size:6px;line-height:13px;text-align:center;color:#555}

/* testimonials */
.testimonials{left:0;top:798px;width:741px;height:192px;background:var(--teal);color:var(--white)}
.testimonials .section-title{color:var(--white);top:21px}
.testimonials .section-intro{color:var(--white);top:43px}
.t-rule{left:112px;top:85px;width:520px;height:1px;background:rgba(255,255,255,.18)}
.quote{top:102px;width:240px;height:66px}
.quote-photo{position:absolute;left:0;top:0;width:66px;height:66px;border-radius:50%}
.quote-body{position:absolute;left:80px;top:2px;width:160px}
.quote-body h4{font-size:7.8px;font-weight:400}
.quote-body time{display:block;font-style:italic;font-size:6.4px;color:#7fe3e5;margin-top:4px}
.quote-body p{font-size:6.5px;line-height:12.5px;margin-top:1px}
.t-arrow{top:126px}

/* footer */
.footer-edge{left:0;top:990px;width:741px;height:3px;background:linear-gradient(90deg,#b95e12,var(--orange),#b95e12)}
.site-footer{left:0;top:993px;width:741px;height:167px;background:linear-gradient(180deg,#191919 0%,var(--footer) 18%,#2f2f2f 100%);color:var(--footer-text);font-family:Lato,sans-serif}
.col-title{position:absolute;top:18px;font-size:11.5px;font-weight:700;color:var(--white);letter-spacing:.2px}
.col-title::after{content:"";position:absolute;left:0;top:18px;width:135px;height:1px;background:#4a4a4a}
.col-divider{position:absolute;top:18px;width:1px;height:118px;background:#444}
.links{position:absolute;top:44px;list-style:none;font-size:9px;line-height:18px}
.links li::before{content:"›";margin-right:5px;font-size:10px}
.news-text{position:absolute;left:270px;top:45px;width:145px;font-size:9px;line-height:13.5px}
.email-input{position:absolute;left:268px;top:80px;width:137px;height:18px;background:linear-gradient(#fff,#e6e6e6);border:1px solid #aaa;border-radius:2px;font-style:italic;font-size:8.5px;color:#777;padding-left:5px;line-height:16px}
.subscribe{position:absolute;left:268px;top:107px;width:78px;height:20px;background:linear-gradient(var(--orange),var(--orange-deep));border-radius:3px;border:1px solid #a84f05;color:#222;font-weight:700;font-size:9.5px;text-align:center;line-height:18px}
.contact{position:absolute;left:443px;top:42px;font-size:9px}
.contact-row{display:flex;align-items:flex-start;gap:9px;line-height:12px}
.contact-row svg{flex:none;margin-top:1px}
.footer-brand{position:absolute;left:616px;top:35px;width:66px;height:66px;border-radius:50%;border:1px solid #5a5a5a;display:flex;align-items:center;justify-content:center;text-align:center;font-size:7.5px;line-height:10px;letter-spacing:1.5px;color:var(--white);text-transform:uppercase}
.follow{position:absolute;left:603px;top:113px;display:flex;align-items:center;gap:3px;font-size:10px;font-weight:700;color:var(--white)}
.follow span{margin-right:4px}
.social{width:16px;height:16px;border-radius:2px;display:block}
.footer-rule{position:absolute;left:85px;top:140px;width:638px;height:1px;background:#3d3d3d}
.copyright{left:0;top:1160px;width:741px;height:40px;background:var(--footer-deep);color:var(--white);text-align:center;font-size:6.8px;font-weight:700;line-height:42px}
</style>
</head>
<body>

<header class="site-header">
  <nav class="main-nav">
    <a class="active" href="#">HOME</a>
    <a href="#">BUYING</a>
    <a href="#">PRESS</a>
    <a href="#">SELLING</a>
    <a href="#">CAREERS</a>
    <a href="#">ABOUT US</a>
  </nav>
</header>
<div class="brand">Meridale<br>Real<br>Estate</div>

<section class="hero">
  <div class="hero-photo" role="img" aria-label="Large illuminated villa with palm trees and a fountain at dusk"></div>
  <div class="hero-arrow" style="left:65px"><svg width="26" height="26"><path d="M15 8 10 13 15 18" fill="none" stroke="#fff" stroke-width="2"/></svg></div>
  <div class="hero-arrow" style="left:649px"><svg width="26" height="26"><path d="M11 8 16 13 11 18" fill="none" stroke="#fff" stroke-width="2"/></svg></div>

  <form class="quick-search">
    <h2>Quick Search</h2>
    <div class="field">Residential Search</div>
    <div class="radios">
      <span class="radio"><i class="on"></i>BUY</span>
      <span class="radio"><i></i>RENT</span>
    </div>
    <div class="field-row"><div class="field">Price Min</div><div class="field">Price Max</div></div>
    <div class="field-row"><div class="field">Bedrooms</div><div class="field">Bathrooms</div></div>
    <div class="field" style="margin-top:11px">All Types</div>
    <div class="suburbs">
      <span class="sel">All Suburbs</span><span>Abbey</span><span>Alfred Cove</span><span>Armadale</span><span>Attadale</span>
    </div>
    <div class="search-btn">Search</div>
  </form>

  <div class="hero-caption">SUPERBLY LOCATED, INVITINGLY READY TO ENJOY
    <div class="hero-dots"><i></i><i></i><i></i><i></i></div>
  </div>
</section>

<div class="abs welcome-photo" role="img" aria-label="Modern two-storey house with lit pool terrace at dusk"></div>
<h1 class="abs welcome-title">Welcome to Meridale Real Estate</h1>
<p class="abs welcome-text">It is a long established fact that a reader will be distracted by the readable content of a page when looking at its layout. The point of using Lorem Ipsum is that it has a more-or-less normal distribution of letters, as opposed to using 'Content here, content here', making it look like readable English. Many desktop publishing packages and web page editors now use Lorem Ipsum as their default model text, and a search for 'lorem ipsum' will uncover many web sites still in their infancy. Various versions have evolved over the years, sometimes by accident, sometimes on purpose</p>
<div class="abs rule"></div>

<h2 class="abs section-title" style="top:533px">FEATURED PROPERTY</h2>
<p class="abs section-intro" style="top:557px">It is a long established fact that a reader will be distracted by the readable content of a page when looking at its layout. The point of using Lorem Ipsum is that it has a more-or-less normal distribution of letters, as opposed to using...</p>
<div class="abs pager">
  <svg width="7" height="10"><path d="M5 1 1 5 5 9" fill="none" stroke="#999" stroke-width="1.3"/></svg>
  <svg width="7" height="10"><path d="M2 1 6 5 2 9" fill="none" stroke="#999" stroke-width="1.3"/></svg>
</div>

<article class="abs card" style="left:107px">
  <div class="card-photo" role="img" aria-label="Peach mansion with a swimming pool" style="background:linear-gradient(180deg,#c89ab0 0%,#d8a98a 45%,#c98a5e 65%,#4d9fc4 100%)"></div>
  <h3>MEXICO CITY</h3><p>Uncover many web sites still in their infancy various versions...</p><span class="more-btn">Read More</span>
</article>
<article class="abs card" style="left:242px">
  <div class="card-photo" role="img" aria-label="Two-storey family house with a green lawn" style="background:linear-gradient(180deg,#9fc3e6 0%,#8e8a85 45%,#6a6258 65%,#4f8f2e 100%)"></div>
  <h3>MEXICO CITY</h3><p>Uncover many web sites still in their infancy various versions...</p><span class="more-btn">Read More</span>
</article>
<article class="abs card" style="left:379px">
  <div class="card-photo" role="img" aria-label="Modern white low house on grass" style="background:linear-gradient(180deg,#6f7c86 0%,#9aa3a6 40%,#e6e2da 65%,#4b6a2a 100%)"></div>
  <h3>MEXICO CITY</h3><p>Uncover many web sites still in their infancy various versions...</p><span class="more-btn">Read More</span>
</article>
<article class="abs card" style="left:516px">
  <div class="card-photo" role="img" aria-label="Stone suburban house under a blue sky" style="background:linear-gradient(180deg,#3e74c2 0%,#7b90b0 40%,#8d7a6c 65%,#4f7d36 100%)"></div>
  <h3>MEXICO CITY</h3><p>Uncover many web sites still in their infancy various versions...</p><span class="more-btn">Read More</span>
</article>

<section class="abs testimonials">
  <h2 class="abs section-title">Testimonials</h2>
  <p class="abs section-intro">It is a long established fact that a reader will be distracted by the readable content of a page when looking at its layout. The point of using Lorem Ipsum is that it has a more-or-less normal distribution of letters, as opposed to using...</p>
  <div class="abs t-rule"></div>
  <svg class="abs t-arrow" style="left:79px" width="9" height="14"><path d="M7 1 2 7 7 13" fill="none" stroke="#fff" stroke-width="2"/></svg>
  <svg class="abs t-arrow" style="left:651px" width="9" height="14"><path d="M2 1 7 7 2 13" fill="none" stroke="#fff" stroke-width="2"/></svg>

  <div class="abs quote" style="left:115px">
    <div class="quote-photo" role="img" aria-label="Small blue model house" style="background:radial-gradient(circle at 50% 45%,#3c78c6 0 30%,#b7c4d4 60%,#7d8894 100%)"></div>
    <div class="quote-body"><h4>Dorian Pell</h4><time>Posted on 27 Mar 2014</time><p>uncover many web sites still in their infancy. Various versions have evolved over the years, sometimes by accident, sometimes on purpose</p></div>
  </div>
  <div class="abs quote" style="left:395px">
    <div class="quote-photo" role="img" aria-label="Model house held in hands" style="background:radial-gradient(circle at 50% 45%,#c9c2bb 0 30%,#8a6f5e 60%,#3d3b44 100%)"></div>
    <div class="quote-body"><h4>Dorian Pell</h4><time>Posted on 27 Mar 2014</time><p>uncover many web sites still in their infancy. Various versions have evolved over the years, sometimes by accident, sometimes on purpose</p></div>
  </div>
</section>

<div class="abs footer-edge"></div>
<footer class="abs site-footer">
  <h3 class="col-title" style="left:97px">QUICK LINKS</h3>
  <ul class="links" style="left:95px"><li>Home</li><li>About Us</li><li>Our Services</li><li>Rental Property</li><li>Property for Sale</li></ul>
  <ul class="links" style="left:177px"><li>Contact Us</li><li>FAQ's</li></ul>
  <div class="col-divider" style="left:250px"></div>

  <h3 class="col-title" style="left:270px">NEWLETTERS &amp; UPDATES</h3>
  <p class="news-text">Get latest updates by entering your email address</p>
  <div class="email-input">Email Address</div>
  <div class="subscribe">SUBSCRIBE</div>
  <div class="col-divider" style="left:425px"></div>

  <h3 class="col-title" style="left:446px">CONTACT INFO</h3>
  <div class="contact">
    <div class="contact-row"><svg width="9" height="11"><path d="M4.5 0C2 0 0 2 0 4.3 0 7.5 4.5 11 4.5 11S9 7.5 9 4.3C9 2 7 0 4.5 0Z" fill="#aaa"/><circle cx="4.5" cy="4.3" r="1.6" fill="#2c2c2c"/></svg><span>Street Name, City Name<br>Zip Code - 00000</span></div>
    <div class="contact-row" style="margin-top:8px"><svg width="10" height="10"><path d="M2 0 4 2.5 3 4Q4.5 6.5 6 7L7.5 6 10 8 8.5 10Q3 9 0 2Z" fill="#aaa"/></svg><span>123-456-7890</span></div>
    <div class="contact-row" style="margin-top:8px"><svg width="10" height="10"><rect x="2" y="0" width="6" height="3" fill="#aaa"/><rect x="0" y="3" width="10" height="5" rx="1" fill="#aaa"/><rect x="2" y="7" width="6" height="3" fill="#ddd"/></svg><span>123-456-7890</span></div>
    <div class="contact-row" style="margin-top:9px"><svg width="10" height="7"><rect width="10" height="7" fill="#aaa"/><path d="M0 0 5 4 10 0" fill="none" stroke="#2c2c2c"/></svg></div>
  </div>
  <div class="col-divider" style="left:580px"></div>

  <div class="footer-brand">Meridale<br>Real<br>Estate</div>
  <div class="follow"><span>Follow Us</span>
    <i class="social" style="background:#3b5ba0"></i>
    <i class="social" style="background:#28a9e1"></i>
    <i class="social" style="background:#1a7bb9"></i>
  </div>
  <div class="footer-rule"></div>
</footer>
<div class="abs copyright">© Copyrights 2015 Meridale Real Estate. All Right Reserved</div>

</body>
</html>
```